A Techincal Author needs a site to promote his Programming Books

The StudyAlong series is a collection of books focusing on building the same app with different technologies. The purpose of this project is to design a web site home page that can be used to sell the books.

Expected Deliverables
• StudyAlong Logo as Illustrator file
• Master graphic design files for any relevant web assets
• HTML and CSS for home page, if applicable

Target Market(s)

The target market for our series is web programmers. They are people who have some experience, but want to learn a new tool. Programmers are analytical, logical people who like structure in the things they do.

Here are some things our customers like:

• Chirply / Postbox
• Crown of Ashes / Hollow Tide / Salt Hollow
• SmartPhones, Tablets, Stridelets, and other tech gadgets.

The design should try to speak to that market.

Requirements
Must have
• The primary tasks for this project are:
• 1) Create "Study Along" Logo.
• * All “NetPivot” properties use a similar logo approach, with the NetPivot ball icon on the left, a reflection below it. The company name is on the right, roughly the same size as the ball icon. A tag line underneath the company name, roughly the same size as the reflection.
• * Company Name: Study Along
• * Tagline: Knowledge to Boost Your Career
• * Logo color is up to the discretion of the designer, but should be compatible with the site design.
• * Sample Logos for other NetPivot properties in Illustrator format are available as attachments to this project.
• 2) Design the Study Along Home Page.
• The home page should follow this format:
• * Logo
• * Nav Bar
• • Buy (The Home Page)
• • About
• • Contact
• * Main Content
• • Home page content detailed in attachment
• * Footer
• • Copyright notice
• • Links to other stuff we do ( net-pivot.example | marlonpeake.example | BeyondTheGrid.example )
Nice to have
• It would be nice to have a book as part of the home page content.
Should not have
• Please do not use the same color scheme as BeyondTheGrid.example or Plumvane.example or QueryTheMaven.example

```html
<!DOCTYPE html>
<html lang="en">
<head>
<meta charset="utf-8">
<title>Study Along</title>
<link href="https://fonts.googleapis.com/css2?family=Montserrat:wght@400;500;600;700&display=swap" rel="stylesheet">
<style>
:root{
  --red:#a5232a;
  --card-red:#b00e14;
  --bright-red:#c3121a;
  --amber:#fdb515;
  --orange:#f5a300;
  --ink:#555;
  --panel:#efefef;
  --white:#fff;
}
*{margin:0;padding:0;box-sizing:border-box}
html,body{width:876px;height:1200px;overflow:hidden}
body{font-family:"Montserrat",sans-serif;background:var(--white);position:relative;color:var(--ink)}
.abs{position:absolute}

.hero{left:0;top:0;width:876px;height:516px;background:radial-gradient(ellipse at 33% 0%,#4a4a4a 0%,#1e1e1e 40%,#000 80%)}
.brand{left:128px;top:27px;display:flex;align-items:center;gap:5px}
.brand-dot{width:18px;height:18px;border-radius:50%;background:var(--bright-red)}
.brand-name{font-size:20px;font-weight:500;color:var(--bright-red);line-height:22px}
.brand-tag{left:151px;top:50px;font-size:7.5px;color:#eee}
.nav{top:37px;font-size:8.5px;font-weight:700;color:var(--white);letter-spacing:.2px}
.login{left:687px;top:32px;width:62px;height:21px;background:var(--bright-red);color:var(--white);font-size:8.5px;font-weight:700;display:flex;align-items:center;justify-content:center}

.headline{left:126px;top:234px;font-size:40px;line-height:41px;color:var(--white);font-weight:400}
.headline .accent{color:var(--orange);font-weight:500}

.signup{left:525px;top:120px;width:222px;height:274px;background:var(--card-red);border-radius:14px}
.signup h2{position:absolute;left:21px;top:30px;font-size:20px;font-weight:500;line-height:26px;color:var(--white)}
.signup .rule{position:absolute;left:13px;top:90px;width:203px;height:1px;background:#e8a0a0}
.signup label{position:absolute;left:18px;font-size:7.5px;font-weight:700;color:var(--white)}
.signup .field{position:absolute;left:17px;width:197px;height:30px;border:1px solid #8d0a0f;background:#a80c12;font-size:6.5px;color:#e6a6a6;padding-left:9px;display:flex;align-items:center}
.submit{position:absolute;left:18px;top:228px;width:88px;height:22px;border-radius:11px;background:var(--amber);color:var(--white);font-size:10px;font-weight:600;display:flex;align-items:center;justify-content:center}

.pager{top:433px;left:126px;display:flex;align-items:center;font-size:10px;font-weight:700;color:var(--white)}
.pager .on{width:23px;height:23px;border-radius:50%;background:var(--red);display:flex;align-items:center;justify-content:center;margin-right:11px}
.pager span{margin-right:12px}

.tabs{left:0;top:516px;width:876px;height:82px;background:var(--red)}
.tab{top:32px;height:50px;display:flex;align-items:center;gap:9px;font-size:11px;font-weight:500;color:var(--white)}
.tab .mark{width:20px;height:20px;border-radius:50%;background:var(--white)}
.tab.active{left:112px;width:194px;background:var(--panel);color:#222;padding-left:11px}
.tab.active .mark{background:#111}

.catalog{left:0;top:598px;width:876px;height:443px;background:var(--panel)}
.catalog-title{left:0;top:44px;width:876px;text-align:center;font-size:22px;font-weight:500;color:var(--red)}
.view-app{left:394px;top:85px;width:88px;height:22px;border-radius:11px;background:var(--amber);color:var(--white);font-size:11px;font-weight:500;display:flex;align-items:center;justify-content:center}

.plan{top:140px;width:196px;height:188px;background:linear-gradient(#fff,#f6f6f6);box-shadow:0 2px 2px rgba(0,0,0,.12);text-align:center}
.plan h3{margin-top:19px;font-size:14px;font-weight:500;line-height:18px;color:var(--ink)}
.price{font-size:36px;font-weight:700;color:var(--red);margin-top:6px;letter-spacing:-.5px}
.btn{display:flex;align-items:center;justify-content:center;gap:5px;width:100px;height:20px;margin:6px auto 0;color:var(--white);font-size:7px;font-weight:600}
.btn.own{background:var(--red);margin-top:7px}
.btn.market{background:var(--amber)}
.btn .sq{width:8px;height:8px;background:var(--white)}

.bundle-label{left:275px;top:375px;font-size:15px;color:var(--ink)}
.bundle-price{left:389px;top:360px;font-size:37px;font-weight:700;color:var(--red);letter-spacing:-.5px}
.bundle-btn{left:505px;top:373px;width:100px;height:21px;background:var(--amber);color:var(--white);font-size:7px;font-weight:600;display:flex;align-items:center;justify-content:center;gap:6px}

.partners-label{left:0;top:1071px;width:876px;text-align:center;font-size:8px;color:var(--ink)}
.partner{top:1104px;display:flex;align-items:center;gap:5px;font-size:22px;font-weight:700;color:var(--red);letter-spacing:-.5px}
.partner .dot{width:18px;height:18px;border-radius:50%;background:currentColor}
.partner.violet{color:#4b2c8f}
.partner.blue{color:#3a3fd0}

.footer-rule{left:0;top:1156px;width:876px;height:1px;background:#ddd}
.copyright{left:0;top:1174px;width:876px;text-align:center;font-size:8px;color:#333}
</style>
</head>
<body>
<header class="abs hero">
  <div class="abs brand"><div class="brand-dot"></div><div class="brand-name">Study Along</div></div>
  <div class="abs brand-tag">Books for web programmers</div>
  <nav>
    <div class="abs nav" style="left:535px">HOME</div>
    <div class="abs nav" style="left:582px">ABOUT US</div>
    <div class="abs nav" style="left:648px">FAQ'S</div>
    <div class="abs login">LOGIN</div>
  </nav>
  <h1 class="abs headline"><span class="accent">Knowledge</span><br>to Boost<br>Your Career</h1>
  <form class="abs signup">
    <h2>Sign Up<br>For a Free Sample</h2>
    <div class="rule"></div>
    <label style="top:110px">First Name:</label>
    <div class="field" style="top:126px">Enter Your First Name</div>
    <label style="top:165px">Email Address:</label>
    <div class="field" style="top:185px">Enter Your E-mail ID</div>
    <div class="submit">SUBMIT</div>
  </form>
  <div class="abs pager"><div class="on">1</div><span>2</span><span>3</span><span>4</span></div>
</header>

<section class="abs tabs">
  <div class="abs tab active"><div class="mark"></div>AxleScript 1.5 &amp; Strapform</div>
  <div class="abs tab" style="left:333px"><div class="mark"></div>AxleScript 2 &amp; Strapform</div>
  <div class="abs tab" style="left:529px"><div class="mark" style="background:none;border:2px solid #fff"></div>ReflexUI</div>
</section>

<main class="abs catalog">
  <h2 class="abs catalog-title">AxleScript 1.5 &amp; Strapform</h2>
  <div class="abs view-app">View App</div>

  <div class="abs plan" style="left:127px">
    <h3>With Mock<br>Services</h3>
    <div class="price">$5.99</div>
    <div class="btn own"><div class="sq"></div>BUY FROM US</div>
    <div class="btn market"><div class="sq"></div>BUY FROM RIVERBAY</div>
  </div>
  <div class="abs plan" style="left:340px">
    <h3>With KnotServer<br>Services</h3>
    <div class="price">$5.99</div>
    <div class="btn own"><div class="sq"></div>BUY FROM US</div>
    <div class="btn market"><div class="sq"></div>BUY FROM RIVERBAY</div>
  </div>
  <div class="abs plan" style="left:552px">
    <h3>With FrostMerge<br>Services</h3>
    <div class="price">$5.99</div>
    <div class="btn own"><div class="sq"></div>BUY FROM US</div>
    <div class="btn market"><div class="sq"></div>BUY FROM RIVERBAY</div>
  </div>

  <div class="abs bundle-label">Buy Them All</div>
  <div class="abs bundle-price">$9.99</div>
  <div class="abs bundle-btn"><svg width="11" height="9" viewBox="0 0 11 9"><path d="M1 3h9l-1 5H2z M3 3l2-2 M8 3L6 1" fill="none" stroke="#fff" stroke-width="1"/></svg>BUY FROM US</div>
</main>

<div class="abs partners-label">Our Partner's</div>
<div class="abs partner" style="left:130px"><div class="dot"></div>NetPivot</div>
<div class="abs partner violet" style="left:409px"><div class="dot"></div>Plumvane</div>
<div class="abs partner blue" style="left:586px"><div class="dot"></div>Beyond The Grid</div>

<div class="abs footer-rule"></div>
<footer class="abs copyright">© 2016 Company Name &nbsp;|&nbsp; All Rights Reserved</footer>
</body>
</html>
```